Healthcare website

We want to replace our website using joomla as the CMS. We want it to be device agnostic (gantry etc). Our business is health care our clients are people with high level spinal cord injuries ( quadriplegia / tetraplegia etc ). The site is a marketing tool primarily to potential clients and a portal for existing staff to access forms etc. It will showcase our key staff and our capability. It will also be where any new recruits apply to work with us. It must allow us to integrate our social media initiatives also. The final design must convey sophistication, high quality care and be warm and welcoming.

current web site is www.tendralwick.com.au
Updates

I have made small change to the brief in that i have removed the prefered color and indicated it would be nice to see some images that symbolize change / transformation like butterflies etc. thank you

Target Market(s)

Our business is health care our clients are people with high level spinal cord injuries ( quadriplegia / tetraplegia etc ).

Industry/Entity Type

Marketing

Colors

Designer to choose colors to be used in the design.

Requirements
Must have
• The site is a marketing tool primarily to potential clients and a portal for existing staff to access forms etc. It will showcase our key staff and our capability. It will also be where any new recruits apply to work with us. It must allow us to integrate our social media initiatives also. The final design must convey sophistication, high quality care and be warm and welcoming.
Nice to have
• Would be nice to incorporate images that symbolize change and new transformations - butterflies etc.

```html
<!DOCTYPE html>
<html lang="en">
<head>
<meta charset="utf-8">
<title>Tendralwick Care – Home</title>
<link rel="stylesheet" href="https://fonts.googleapis.com/css2?family=Open+Sans:wght@400;600;700&family=Dancing+Script:wght@700&display=swap">
<style>
:root{
  --blue:#2f74b9;
  --blue-dark:#1f5589;
  --navy:#2b2d55;
  --pink:#e9457a;
  --gold:#f5b400;
  --text:#555;
  --muted:#9a9a9a;
  --panel:#ebebeb;
  --page-bg:#eceef1;
  --white:#fff;
}
*{box-sizing:border-box;margin:0;padding:0}
html,body{width:1200px;height:2748px;overflow:hidden}
body{position:relative;background:var(--page-bg);font-family:"Open Sans",Arial,sans-serif;color:var(--text);font-size:13px}
.abs{position:absolute}
.page{position:absolute;left:84px;top:0;width:1032px;height:2131px;background:var(--white);box-shadow:0 0 8px rgba(0,0,0,.08)}
.topline{position:absolute;left:0;top:0;width:1200px;height:3px;background:var(--blue)}

/* header */
.brand{left:101px;top:50px;display:flex;align-items:center;gap:10px;font-size:26px;font-weight:600;color:var(--blue)}
.brand-dot{width:28px;height:28px;border-radius:50%;background:var(--blue)}
.search{left:835px;top:44px;width:264px;height:29px;display:flex}
.search-field{flex:1;background:#e6e6e6;font-size:11px;color:#888;padding:7px 10px}
.search-btn{width:32px;background:var(--blue);display:flex;align-items:center;justify-content:center}
.nav{left:101px;top:121px;width:998px;height:40px;background:var(--blue);display:flex}
.nav a{display:block;color:var(--white);text-decoration:none;font-size:13px;font-weight:600;line-height:40px;padding:0 31px}
.nav a.active{background:var(--blue-dark)}

/* hero */
.hero{left:101px;top:176px;width:998px;height:458px;border:1px solid #e2e2e2;
  background:linear-gradient(90deg,#dde8ee 0%,#eef2f4 18%,#c9d2da 34%,#f1f3f4 48%,#e4cdbd 64%,#d9b8a3 72%,#eef0f2 84%,#c7ccd3 100%)}
.hero-arrow{width:28px;height:28px;border-radius:50%;background:rgba(47,116,185,.55);display:flex;align-items:center;justify-content:center}
.hero-cap{left:154px;font-size:16px;color:var(--white);padding:0 16px;line-height:44px}
.hero-cap.primary{top:491px;width:449px;background:rgba(47,116,185,.9)}
.hero-cap.secondary{top:537px;width:266px;background:rgba(45,45,60,.8)}

/* welcome */
.section-title{font-size:23px;font-weight:600;color:var(--navy);text-transform:uppercase}
.welcome-title{left:0;width:1200px;top:686px;text-align:center}
.tagline{left:0;width:1200px;top:733px;text-align:center;font-family:"Dancing Script",cursive;font-weight:700;font-size:18px;color:#666}
.intro{left:150px;width:900px;top:776px;text-align:center;font-size:12.5px;line-height:19px}
.stats{left:0;width:1200px;top:920px;display:flex;justify-content:center;gap:30px;align-items:center}
.stat{display:flex;align-items:center;gap:12px}
.stat-num{font-family:"Dancing Script",cursive;font-weight:700;font-size:44px;line-height:1;color:var(--navy)}
.stat-num.pink{color:var(--pink)}
.stat-label{font-size:12px;line-height:15px;color:var(--navy)}
.stat-label.pink{color:var(--pink)}
.btn{display:inline-block;background:var(--blue);color:var(--white);font-size:12px;font-weight:600;text-align:center;line-height:26px}
.btn.navy{background:var(--blue-dark)}

.heading{font-size:23px;font-weight:600;color:var(--navy);text-transform:uppercase}
.pager{display:flex;gap:5px}
.pager span{width:17px;height:17px;display:flex;align-items:center;justify-content:center;background:#aaa}
.pager span.on{background:var(--blue)}

/* team */
.member{width:200px;text-align:center}
.member-photo{position:relative;width:123px;height:123px;margin:0 auto;border-radius:50%}
.member-no{position:absolute;left:-16px;top:47px;width:33px;height:33px;border-radius:50%;background:var(--blue);color:var(--white);font-weight:700;font-size:14px;line-height:29px;border:2px solid var(--white)}
.member-name{margin-top:19px;font-size:18px;color:#222}
.member-role{margin-top:6px;font-size:11px;color:var(--muted)}
.member-social{margin-top:22px;display:flex;justify-content:center;gap:34px}
.member-social i{display:block;width:11px;height:11px;border-radius:50%}

/* news */
.news{left:769px;top:1099px;width:330px;height:372px;background:var(--panel);padding:22px 20px}
.news h3{font-size:15px;font-weight:700;color:#333}
.news p{margin-top:8px;font-size:11px;line-height:17px;font-weight:600;color:#666}
.news ul{list-style:none;margin-top:18px}
.news li{position:relative;padding-left:24px;padding-right:14px;font-size:12.5px;line-height:17px;color:var(--blue);font-weight:600;margin-bottom:16px}
.news li::before{content:"";position:absolute;left:4px;top:6px;width:6px;height:6px;border-radius:50%;background:var(--blue)}

/* gallery */
.gallery-text{left:101px;top:1458px;width:628px;font-size:12.5px;line-height:19px}
.gallery-item{top:1532px;width:196px;text-align:center}
.gallery-photo{height:146px}
.gallery-item span{display:block;margin-top:25px;font-size:13px;color:#333}

/* join */
.join{left:769px;top:1550px;width:330px;height:172px;background:var(--blue);padding:24px 22px;color:var(--white);font-size:12.5px;font-weight:600;line-height:19px}
.join p+p{margin-top:17px}

/* licensed */
.licensed-title{left:0;width:1200px;top:1809px;text-align:center}
.licensed-text{left:115px;width:970px;top:1857px;text-align:center;font-size:12.5px;line-height:19px}
.badges{left:101px;top:1936px;width:998px;height:127px;background:var(--blue);display:flex;gap:29px;padding:26px 0 0 27px}
.badge{width:110px;height:77px;border:1px solid rgba(255,255,255,.35);display:flex;align-items:center;justify-content:center}
.badge i{display:block;background:rgba(255,255,255,.9)}
.badge .round{width:36px;height:36px;border-radius:50%}
.badge .wide{width:62px;height:22px;border-radius:2px}
.badge .tall{width:30px;height:52px;border-radius:2px}
.badge .square{width:38px;height:38px;border-radius:4px}

/* map + contact */
.map{left:0;top:2131px;width:1200px;height:540px;background:linear-gradient(100deg,#e6e2da 0%,#dcd8cf 22%,#d4dcc6 32%,#e4e0d8 45%,#dedad2 70%,#d6dfc9 86%,#e5e1d9 100%)}
.contact{left:398px;top:2268px;width:430px;height:403px;background:var(--blue);text-align:center;color:var(--white)}
.contact-bar{position:absolute;left:181px;top:0;width:66px;height:5px;background:var(--gold)}
.contact h2{margin-top:56px;font-size:25px;font-weight:400;color:var(--gold)}
.contact address{margin-top:10px;font-style:normal;font-size:11.5px;line-height:18px;font-weight:600}
.field{position:absolute;border:1px solid rgba(255,255,255,.75);font-size:10px;text-align:left;padding:8px 10px}

/* footer */
.footer{left:0;top:2671px;width:1200px;height:77px;background:var(--blue);color:var(--white)}
.footer-links{position:absolute;left:449px;top:12px;display:flex;gap:33px;font-size:10px}
.footer-copy{position:absolute;left:101px;top:50px;font-size:10.5px}
.footer-social{position:absolute;left:990px;top:52px;display:flex;gap:20px}
.footer-social i{display:block;width:10px;height:10px;border-radius:50%;background:var(--white)}
.to-top{position:absolute;left:1139px;top:40px;width:25px;height:25px;border:1px solid var(--white);display:flex;align-items:center;justify-content:center}
</style>
</head>
<body>
<div class="topline"></div>
<div class="page"></div>

<header>
  <div class="abs brand"><span>Tendralwick Care</span><span class="brand-dot"></span></div>
  <div class="abs search">
    <div class="search-field">Search Here</div>
    <div class="search-btn"><svg width="12" height="12" viewBox="0 0 12 12"><circle cx="5" cy="5" r="3.6" fill="none" stroke="#fff" stroke-width="1.6"/><line x1="7.6" y1="7.6" x2="11" y2="11" stroke="#fff" stroke-width="1.8"/></svg></div>
  </div>
  <nav class="abs nav">
    <a class="active" href="#">HOME</a><a href="#">ABOUT US</a><a href="#">OUR TEAM</a><a href="#">FAQ</a><a href="#">OUR SERVICES</a><a href="#">RESOURCES</a><a href="#">CONTACT US</a>
  </nav>
</header>

<section>
  <div class="abs hero" role="img" aria-label="Photo of a smiling doctor with a stethoscope, medical staff in the background"></div>
  <div class="abs hero-arrow" style="left:133px;top:378px"><svg width="10" height="12" viewBox="0 0 10 12"><path d="M7 1 2 6l5 5" fill="none" stroke="#fff" stroke-width="2"/></svg></div>
  <div class="abs hero-arrow" style="left:1043px;top:378px"><svg width="10" height="12" viewBox="0 0 10 12"><path d="M3 1l5 5-5 5" fill="none" stroke="#fff" stroke-width="2"/></svg></div>
  <div class="abs hero-cap primary">We are a high level spinal cord injuries treatment center</div>
  <div class="abs hero-cap secondary">( quadriplegia / tetraplegia etc )</div>
</section>

<section>
  <h1 class="abs section-title welcome-title">Welcome to Tendralwick Care</h1>
  <div class="abs tagline">what is it for?</div>
  <p class="abs intro">Tendralwick Care is a small team of care professionals committed to providing quality one-to-one care with heart.<br>Tendralwick Care has built its service around the needs of each and every client. We listen to and consult with our clients, their families, Care Teams and the wider care community. Tendralwick Care is a privately owned organisation providing in home care for people with disabilities (attendant care) throughout the State of Victoria. We commenced operation on the 1st of July 2004 at our principal office in Ferrow Vale, Victoria.<br>We are committed to our Vision - "to provide the BEST care" and we are fully accountable to our clients, carers and funding organisations. We are solely focused on providing the best care and we continuously innovate to ensure we do this.</p>
  <div class="abs stats">
    <div class="stat"><span class="stat-num">1428</span><span class="stat-label">happy<br>customers</span></div>
    <div class="stat"><span class="stat-num pink">8k</span><span class="stat-label pink">social<br>followers</span></div>
  </div>
  <a class="abs btn" style="left:549px;top:989px;width:119px">Read More</a>
</section>

<section>
  <h2 class="abs heading" style="left:101px;top:1048px">Our Team</h2>
  <div class="abs pager" style="left:684px;top:1050px"><span class="on"><svg width="6" height="8"><path d="M6 0v8L0 4z" fill="#fff"/></svg></span><span><svg width="6" height="8"><path d="M0 0v8l6-4z" fill="#fff"/></svg></span></div>
  <div class="abs member" style="left:85px;top:1108px">
    <div class="member-photo" role="img" aria-label="Portrait of the chief executive officer" style="background:radial-gradient(circle at 50% 45%,#d9a98c 0%,#a66a4c 40%,#4a2e24 80%)"><span class="member-no">1</span></div>
    <div class="member-name">Marisol Quennell</div>
    <div class="member-role">Chief Executive Officer</div>
    <div class="member-social"><i style="background:#3b5998"></i><i style="background:#4aa3df"></i><i style="background:#e9457a"></i></div>
  </div>
  <div class="abs member" style="left:309px;top:1108px">
    <div class="member-photo" role="img" aria-label="Portrait of the UI/UX strategist" style="background:radial-gradient(circle at 50% 50%,#f0cfb0 0%,#e2c07e 35%,#b5432f 62%,#7a1f18 90%)"><span class="member-no">2</span></div>
    <div class="member-name">Dora Halvenstrom</div>
    <div class="member-role">Black Belt UI/UX Strategist</div>
    <div class="member-social"><i style="background:#3b5998"></i><i style="background:#4aa3df"></i><i style="background:#e9457a"></i></div>
  </div>
  <div class="abs member" style="left:547px;top:1108px">
    <div class="member-photo" role="img" aria-label="Group photo of the care team" style="background:radial-gradient(circle at 50% 45%,#c89a86 0%,#6b4a48 45%,#1e1a20 85%)"><span class="member-no">3</span></div>
    <div class="member-name">Bram Oakhurst</div>
    <div class="member-role">Lead User Experience Manager</div>
    <div class="member-social"><i style="background:#3b5998"></i><i style="background:#4aa3df"></i><i style="background:#e9457a"></i></div>
  </div>

  <h2 class="abs heading" style="left:769px;top:1048px">Disability News</h2>
  <aside class="abs news">
    <h3>Spinal Recovery Desk</h3>
    <p>The latest Spinal Cord Injury News, Information and Resources for People living with SCI Spinal Cord Injury</p>
    <ul>
      <li>New Methods Show Promise for Rehabilitating Paralyzed Patients With Spinal Cord Injury</li>
      <li>Stem-cell advances may quell ethics debate</li>
      <li>Wheelchair rugby a family affair for mom and son</li>
      <li>Stem Cells Fast Facts</li>
      <li>Attitude can play significant role in recovery from paralyzing injury</li>
    </ul>
  </aside>
</section>

<section>
  <h2 class="abs heading" style="left:101px;top:1418px">Our Gallery</h2>
  <div class="abs pager" style="left:684px;top:1420px"><span class="on"><svg width="6" height="8"><path d="M6 0v8L0 4z" fill="#fff"/></svg></span><span><svg width="6" height="8"><path d="M0 0v8l6-4z" fill="#fff"/></svg></span></div>
  <p class="abs gallery-text">Lorem ipsum dolor sit amet, consectetur adipiscing elit. Proin tincidunt ullamcorper velit, et euismod dui ornare nec. Donec sagittis vestibulum nibh.</p>
  <figure class="abs gallery-item" style="left:101px"><div class="gallery-photo" role="img" aria-label="Photo of smiling men gathered together" style="background:linear-gradient(170deg,#2f3b26 0%,#5d6e3c 25%,#c9977a 50%,#f2f0ec 75%,#d9d6d2 100%)"></div><span>Lorem Ipsum Dolor</span></figure>
  <figure class="abs gallery-item" style="left:317px"><div class="gallery-photo" role="img" aria-label="Photo of a group celebrating with blue balloons" style="background:linear-gradient(180deg,#3d3438 0%,#7a5e5a 30%,#a9776c 55%,#2d5fae 78%,#1f4b95 100%)"></div><span>Lorem Ipsum Dolor</span></figure>
  <figure class="abs gallery-item" style="left:533px"><div class="gallery-photo" role="img" aria-label="Photo of people on a boat deck" style="background:linear-gradient(90deg,#7d7a74 0%,#e6e8e8 20%,#c9ced1 50%,#a39e97 75%,#6c665e 100%)"></div><span>Lorem Ipsum Dolor</span></figure>

  <h2 class="abs heading" style="left:769px;top:1498px">Join Our Team</h2>
  <div class="abs join">
    <p>We are always on the lookout for great people to work with our clients.</p>
    <p>If you want to be a part of our Team click below to apply.</p>
  </div>
  <a class="abs btn navy" style="left:881px;top:1678px;width:117px">Read More</a>
</section>

<section>
  <h2 class="abs section-title licensed-title">Licensed</h2>
  <p class="abs licensed-text">Tendralwick Care is proud to be an approved provider for Road Injury Cover Board (RICB), State Workplace Care Authority (SWCA), Department of Community Services (DCS) and maintain associations and cooperative relationships with a variety of private and governmental organisations in its efforts to bring the finest, most up-to-date care for its clients.</p>
  <div class="abs badges">
    <div class="badge"><i class="round"></i></div>
    <div class="badge"><i class="wide"></i></div>
    <div class="badge"><i class="wide"></i></div>
    <div class="badge"><i class="round"></i></div>
    <div class="badge"><i class="wide"></i></div>
    <div class="badge"><i class="tall"></i></div>
    <div class="badge"><i class="square"></i></div>
  </div>
</section>

<section>
  <div class="abs map" role="img" aria-label="Street map of the surrounding city area"></div>
  <div class="abs contact">
    <span class="contact-bar"></span>
    <h2>Contact Us Now</h2>
    <address>Tendralwick Care - Northside<br>42 - 44 Larchmont Rise<br>Ferrow Vale</address>
    <div class="field" style="left:38px;top:183px;width:170px;height:35px">Name</div>
    <div class="field" style="left:221px;top:183px;width:171px;height:35px">Email</div>
    <div class="field" style="left:38px;top:231px;width:354px;height:95px">Message</div>
    <svg class="abs" style="left:197px;top:356px" width="38" height="26" viewBox="0 0 38 26"><rect x="1" y="1" width="30" height="22" fill="#fff"/><path d="M1 1l15 12L31 1" fill="none" stroke="#2f74b9" stroke-width="1.5"/><path d="M26 18l10-4-4 10" fill="none" stroke="#e9457a" stroke-width="2"/></svg>
  </div>
</section>

<footer class="abs footer">
  <div class="footer-links"><span>Home</span><span>Features</span><span>Shop</span><span>Blog</span><span>Work</span><span>Contact</span></div>
  <div class="footer-copy">tendralwick.com.au © Copyright 2014, all rights reserved</div>
  <div class="footer-social"><i></i><i></i><i></i><i></i></div>
  <div class="to-top"><svg width="10" height="7" viewBox="0 0 10 7"><path d="M1 6l4-4 4 4" fill="none" stroke="#fff" stroke-width="1.6"/></svg></div>
</footer>
</body>
</html>
```